"Vine Hollow Excursions" is a top notch Santa Barbara County Wine Tour company.

We provide scenic, boutique and custom wine tours. I need the card to be clean and classy. I will provide our logo. I would like the logo to cover the back side of the card as an option and would like to see a couple color options other then our signature green and gold. I would like to see some creative options and let the designers come up with options.
I need cards for myself and my team. The final design should communicate "An authentic and boutique wine tour experience"
Please use my website for reference www.vinehollowexcursions.example

Target Market(s)

We have a wide range of clients from millennials to baby boomers

Industry/Entity Type

Tour

Contact Information for Business Card

Contact info:
Dale Morton
805-219-6384
info@vinehollowexcursions.example
vinehollowexcursions.example

Colors

Designer to choose colors to be used in the design.

Requirements
Must have
• my logo
Nice to have
• *I would like to have the backside side with the logo and the company statement
• "An authentic and boutique wine tour experience" as an option.
• *I would also like to see what the designers can create!
• *I would like to see an option that incorporates or social: instagram, yelp, trip advisor
Should not have
• I do not want it too busy.

```html
<!DOCTYPE html>
<html lang="en">
<head>
<meta charset="utf-8">
<title>Vine Hollow Excursions – Business Card</title>
<link rel="stylesheet" href="https://fonts.googleapis.com/css2?family=Cinzel:wght@600&family=Mulish:wght@400&display=swap">
<style>
  :root {
    --backdrop: #5e5e5e;
    --paper: #ffffff;
    --wine: #7a1c4f;
    --wine-deep: #4a0c2e;
    --wine-glow: #7e2559;
    --ink: #3a3a3a;
    --gold: #c9a04f;
    --rule: #b9a9b1;
  }
  * { box-sizing: border-box; margin: 0; padding: 0; }
  html, body { width: 1200px; height: 1008px; overflow: hidden; }
  body { background: var(--backdrop); position: relative; }

  .card { position: absolute; left: 320px; width: 560px; height: 320px; overflow: hidden; }

  /* Front */
  .card-front { top: 166px; background: var(--paper); }
  .brand-name {
    position: absolute; left: 20px; width: 250px; top: 112px;
    text-align: center;
    font-family: "Cinzel", serif; font-weight: 600;
    font-size: 24px; line-height: 30px; letter-spacing: 1px;
    color: var(--wine);
  }
  .divider { position: absolute; left: 279px; top: 78px; width: 1px; height: 163px; background: var(--rule); }
  .contact { position: absolute; left: 294px; top: 86px; font-family: "Mulish", sans-serif; color: var(--ink); }
  .person-name { font-family: "Cinzel", serif; font-weight: 600; font-size: 16px; color: var(--wine); letter-spacing: 0.5px; line-height: 20px; }
  .person-title { font-size: 14.5px; line-height: 20px; margin-top: 2px; }
  .address { font-size: 14.5px; line-height: 20px; margin-top: 7px; }
  .channels { list-style: none; margin-top: 5px; }
  .channels li { display: flex; align-items: center; gap: 5px; font-size: 14px; line-height: 21px; }
  .channels svg { width: 14px; height: 14px; flex: none; }

  /* Back */
  .card-back { top: 527px; }
  .back-field {
    position: absolute; inset: 0;
    background: radial-gradient(ellipse at 50% 80%, var(--wine-glow) 0%, #651645 45%, var(--wine-deep) 100%);
  }
  .back-name {
    position: absolute; left: 0; right: 0; top: 128px; text-align: center;
    font-family: "Cinzel", serif; font-weight: 600; font-size: 28px; letter-spacing: 1.5px;
    color: #ffffff;
  }
  .social { position: absolute; left: 0; right: 0; top: 255px; display: flex; justify-content: center; gap: 12px; }
  .social span { width: 16px; height: 16px; border-radius: 50%; background: var(--gold); }
  .tagline {
    position: absolute; left: 0; right: 0; top: 283px; text-align: center;
    font-family: "Cinzel", serif; font-weight: 600; font-size: 13px; letter-spacing: 0.6px;
    color: #ffffff;
  }
</style>
</head>
<body>
  <section class="card card-front">
    <div class="brand-name">Vine Hollow<br>Excursions</div>
    <div class="divider"></div>
    <div class="contact">
      <div class="person-name">DALE MORTON</div>
      <div class="person-title">Your Title</div>
      <div class="address">Your Address Goes Here<br>Address Line 2</div>
      <ul class="channels">
        <li><svg viewBox="0 0 14 14"><circle cx="7" cy="7" r="7" fill="var(--wine)"/><rect x="3.5" y="4.5" width="7" height="5" fill="none" stroke="#fff" stroke-width="1"/><path d="M3.5 4.5 L7 7.5 L10.5 4.5" fill="none" stroke="#fff" stroke-width="1"/></svg>info@vinehollowexcursions.example</li>
        <li><svg viewBox="0 0 14 14"><circle cx="7" cy="7" r="7" fill="var(--wine)"/><path d="M3.5 6 Q7 3 10.5 6 L9.5 7 L8.5 6 L5.5 6 L4.5 7 Z" fill="#fff"/><rect x="4.5" y="7.3" width="5" height="3" rx="0.5" fill="#fff"/></svg>805-219-6384</li>
        <li><svg viewBox="0 0 14 14"><circle cx="7" cy="7" r="7" fill="var(--wine)"/><circle cx="7" cy="7" r="3.8" fill="none" stroke="#fff" stroke-width="0.9"/><ellipse cx="7" cy="7" rx="1.6" ry="3.8" fill="none" stroke="#fff" stroke-width="0.9"/><line x1="3.2" y1="7" x2="10.8" y2="7" stroke="#fff" stroke-width="0.9"/></svg>vinehollowexcursions.example</li>
      </ul>
    </div>
  </section>

  <section class="card card-back">
    <div class="back-field" role="img" aria-label="Soft wine-coloured backdrop where a faint sunburst over vineyard rows belongs"></div>
    <div class="back-name">VINE HOLLOW EXCURSIONS</div>
    <div class="social" aria-label="Social profiles"><span></span><span></span><span></span></div>
    <div class="tagline">AN AUTHENTIC AND BOUTIQUE WINE TOUR EXPERIENCE</div>
  </section>
</body>
</html>
```